Re designing of website of VELTRIS Pens, an International stationary brand

We would like to re design our existing website veltrispens.com. We are leading manufacturers and exporters of stationary products. Our existence is global -selling and marketing in all 5 continents.

We are a 35year old group with focus on high quality, innovative designs and state of art manufacturing setup.

Client satisfaction by committed service and trust are the roots of our organisation.

We would like to see a website which focuses on our brand Veltris and must have an international appeal. Our target buyers would be Agents, distributors and wholesalers in various countries. Content would be similar to our existing website but designing and outlook needs to be totally different.

For the outlook we do like the following websites from our industry which can be used to draw inspiration.
1. www.duniverastationery.com
2. www.quorlapen.com
3. www.haltmivopen.com

The homepage need not be focused on the product but must emphasis on the branding of Veltris, our existence of 35years along with international presence and quality standards maintained by our organisation.
Updates

Reason: Would like to see some more concepts and designs as per artwork attached.

Target Market(s)

Wholesalers, Agents and Distributors in all countries around the world. Target market is global

Number of Pages Required

1 page

Font styles to use
Sans Serif

Requirements
Must have
• Focus on Branding, High Quality Standards, Customer Loyalty
Nice to have
• Like the outlook of the websites
• www.haltmivopen.com
• www.duniverastationery.com
• www.quorlapen.com
Should not have
• Don't like the outlook of our present website www.veltrispens.com
• It doesn't justify our brand or our product

```html
<!DOCTYPE html>
<html lang="en">
<head>
<meta charset="utf-8">
<title>VELTRIS Pens – World Class Writing Instruments</title>
<link href="https://fonts.googleapis.com/css2?family=Roboto:ital,wght@0,300;0,400;0,500;1,400&family=Oswald:wght@400&family=Raleway:wght@500&display=swap" rel="stylesheet">
<style>
:root{
  --red:#cc2027;
  --red-dark:#b51a20;
  --nav:#2b2b2b;
  --ink:#2e2e2e;
  --text:#333;
  --hero-a:#f2f9fd;
  --hero-b:#cfe9f7;
  --band:#f7f7f9;
  --footer:#4aafe2;
  --bottom:#333333;
  --white:#fff;
}
*{box-sizing:border-box;margin:0;padding:0}
html,body{width:958px;height:1200px;overflow:hidden}
body{position:relative;font-family:"Roboto",sans-serif;color:var(--text);background:var(--white)}

.topbar{position:absolute;left:0;top:0;width:958px;height:71px;background:var(--red)}
.brand{position:absolute;left:72px;top:17px;display:flex;align-items:center;gap:8px;color:var(--white)}
.brand-mark{width:28px;height:28px;background:var(--white);border-radius:2px}
.brand-name{font-size:27px;font-weight:400;line-height:1;letter-spacing:.5px}
.brand-tag{position:absolute;left:36px;top:28px;font-size:8.5px;white-space:nowrap}
.callus{position:absolute;right:77px;top:26px;display:flex;align-items:center;gap:9px;color:var(--white);font-size:13px}
.callus svg{width:24px;height:24px}

.mainnav{position:absolute;left:0;top:71px;width:958px;height:48px;background:var(--nav)}
.mainnav ul{list-style:none;display:flex;position:absolute;left:71px;top:0;height:48px}
.mainnav li{height:48px;line-height:48px;color:var(--white);font-size:12px;padding:0 22.5px}
.mainnav li.active{background:var(--red);padding:0 24px}

.hero{position:absolute;left:0;top:119px;width:958px;height:398px;background:radial-gradient(ellipse at 45% 45%,var(--hero-a) 35%,var(--hero-b) 100%)}
.hero-title{position:absolute;left:79px;top:165px;font-family:"Oswald",sans-serif;font-weight:400;text-transform:uppercase;line-height:1;white-space:nowrap}
.hero-title .l1{display:block;color:var(--red);font-size:21.5px;letter-spacing:-.6px}
.hero-title .l2{display:block;color:var(--ink);font-size:28px;margin-top:13px;letter-spacing:-.7px}
.slider-dots{position:absolute;left:83px;top:267px;display:flex;gap:4px}
.slider-dots span{width:31px;height:3px;background:var(--ink)}
.slider-dots span.on{background:var(--red)}
.hero-visual{position:absolute;left:480px;top:53px;width:408px;height:288px;border-radius:4px;background:linear-gradient(120deg,#2a3b94 0%,#7d7f86 35%,#e0772f 55%,#f4f4f4 72%,#1f2a6a 100%)}

.welcome{position:absolute;left:0;top:540px;width:958px;text-align:center}
.welcome h1{font-family:"Raleway",sans-serif;font-weight:500;font-size:19px;color:var(--ink)}
.welcome h1 em{font-style:normal;color:var(--red)}
.welcome p{width:810px;margin:16px auto 0;font-size:11.5px;line-height:19.5px;color:var(--text)}

.band{position:absolute;left:0;top:840px;width:958px;height:117px;background:var(--band)}
.cards{position:absolute;left:71px;top:673px;display:flex}
.card{width:189px;height:244px;background:var(--white);box-shadow:0 1px 2px rgba(0,0,0,.25);text-align:center}
.card + .card{margin-left:21px}
.card:nth-child(3){margin-left:20px}
.card:nth-child(4){margin-left:18px}
.card-media{height:162px;background:radial-gradient(ellipse at center,#fff 30%,#d8d8d8 100%)}
.card h2{margin-top:13px;font-size:13px;font-weight:400;color:var(--red)}
.card p{margin-top:6px;font-size:9px;line-height:15px;color:var(--text)}

.footer{position:absolute;left:0;top:957px;width:958px;height:171px;background:var(--footer);color:var(--white)}
.fcol{position:absolute;top:36px}
.fcol h3{font-size:10.5px;font-weight:400;letter-spacing:.2px}
.fcol ul{list-style:none;margin-top:13px}
.fcol li{font-size:9.5px;line-height:17px;padding-left:1px}
.quote{margin-top:13px;width:165px;font-size:8px;font-style:italic;line-height:13.5px}
.quote-by{margin-top:6px;font-size:8px}
.signup p{margin-top:12px;width:160px;font-size:8.5px;line-height:12.5px}
.signup .field{margin-top:7px;width:166px;height:24px;background:var(--white);border:1px solid #9cc;color:#555;font-size:8px;line-height:22px;padding-left:8px}
.signup .btn{margin-top:7px;width:64px;height:20px;background:linear-gradient(#f5f5f5,#c9c9c9);border-radius:2px;color:#333;font-size:7.5px;font-weight:500;line-height:20px;text-align:center}
.social{list-style:none;margin-top:11px}
.social li{display:flex;align-items:center;gap:10px;height:20px;margin-bottom:13px;font-size:9px}
.social .dot{width:20px;height:20px;border-radius:50%;background:var(--white);border:2px solid #d9eef9}
.social .dot.alt{background:var(--red-dark)}

.bottombar{position:absolute;left:0;top:1128px;width:958px;height:72px;background:var(--bottom);color:var(--white);text-align:center;font-size:10px;line-height:72px}
</style>
</head>
<body>

<header class="topbar">
  <div class="brand">
    <span class="brand-mark"></span>
    <span class="brand-name">VELTRIS</span>
    <span class="brand-tag">World Class Writing Instruments</span>
  </div>
  <div class="callus">
    <svg viewBox="0 0 24 24" aria-hidden="true"><circle cx="12" cy="12" r="11" fill="none" stroke="#fff" stroke-width="1.2"/><path d="M9.2 7.5c.4-.2.8 0 1 .4l.7 1.6c.1.3 0 .7-.3.9l-.7.5c.5 1.2 1.4 2.1 2.6 2.7l.5-.7c.2-.3.6-.4.9-.2l1.6.7c.4.2.6.6.4 1l-.4 1c-.2.4-.6.7-1 .6-3.5-.4-6.3-3.2-6.7-6.7 0-.4.2-.8.6-1z" fill="#fff"/></svg>
    <span>CALL US : (+91-22) 4410 2387</span>
  </div>
</header>

<nav class="mainnav">
  <ul>
    <li class="active">HOME</li>
    <li>ABOUT US</li>
    <li>RETAIL PRODUCTS</li>
    <li>PROMOTIONAL PRODUCTS</li>
    <li>CAREERS</li>
    <li>ENQUIRY FROM</li>
    <li>CONTACT US</li>
  </ul>
</nav>

<section class="hero">
  <h2 class="hero-title">
    <span class="l1">Veltris goal is just to give best services,</span>
    <span class="l2">but to give legendary services.</span>
  </h2>
  <div class="slider-dots"><span></span><span class="on"></span><span></span><span></span><span></span></div>
  <div class="hero-visual" role="img" aria-label="Box of ballpoint pens beside spiral notebooks and a college refill pad"></div>
</section>

<section class="welcome">
  <h1>WELCOME TO <em>VELTRISPENS</em></h1>
  <p>For 35 years Veltris has crafted writing instruments and stationery built on high quality, innovative design and a state of the art manufacturing setup. Today our products are sold and marketed across all 5 continents through trusted agents, distributors and wholesalers, and every pen leaves our plant checked against strict international quality standards. Committed service and lasting trust keep our clients coming back.</p>
</section>

<div class="band"></div>
<div class="cards">
  <article class="card">
    <div class="card-media" role="img" aria-label="Five click pens in purple, navy, red, green and silver"></div>
    <h2>Pen Configurator</h2>
    <p>Design pens to your own spec,<br>backed by 35 years of craft.</p>
  </article>
  <article class="card">
    <div class="card-media" role="img" aria-label="Colourful spiral note books"></div>
    <h2>Note Book</h2>
    <p>Quality paper checked to strict<br>international standards.</p>
  </article>
  <article class="card">
    <div class="card-media" role="img" aria-label="Red counter display stand filled with pen packs"></div>
    <h2>Packaging</h2>
    <p>Retail-ready displays shipped<br>to buyers on 5 continents.</p>
  </article>
  <article class="card">
    <div class="card-media" role="img" aria-label="Boxed set of whiteboard markers"></div>
    <h2>Office stationery</h2>
    <p>Reliable supply and service<br>that earns lasting loyalty.</p>
  </article>
</div>

<footer class="footer">
  <div class="fcol" style="left:77px">
    <h3>QUICK LINKS</h3>
    <ul><li>Home</li><li>About us</li><li>Careers</li><li>Enquiry From</li><li>Contact Us</li></ul>
  </div>
  <div class="fcol" style="left:219px">
    <h3>SUPPORT LINKS</h3>
    <ul><li>Retail products</li><li>Promotional products</li><li>Office Stationery</li><li>Art Material</li><li>Metal Pens</li></ul>
  </div>
  <div class="fcol" style="left:364px">
    <h3>CLIENT'S TESTIMONIALS</h3>
    <p class="quote">&ldquo; &nbsp;Lorem Ipsum has been the industry's standard dummy text ever since the 1500s, when an unknown printer took a galley of type and scrambled it to make a type specimen book. It has survived not only five cen-</p>
    <p class="quote-by">Client name, City</p>
  </div>
  <div class="fcol signup" style="left:599px">
    <h3>NEWSLETTERS SIGN UP</h3>
    <p>Sign up for our daily email by entering your information below</p>
    <div class="field">Email address</div>
    <div class="btn">SUBSCRIBE</div>
  </div>
  <div class="fcol" style="left:821px">
    <h3>FOLLOW US</h3>
    <ul class="social">
      <li><span class="dot"></span>Friendsy</li>
      <li><span class="dot"></span>Chirper</li>
      <li><span class="dot alt"></span>Circlr</li>
    </ul>
  </div>
</footer>

<div class="bottombar">Copyright © 2015 &nbsp;All Rights Reserved</div>

</body>
</html>
```